Innovation Company Business Card Design

I need to have my business card updated. The current card was designed when the company started 2.5 years ago and was a quick and dirty job.

I need a new card design that is more professional and has my updated company tag line.

I will include the old card's Corel Draw file, and EPS versions as examples of the current design. I will also include the company logo eps and corel version files.

The company pantone colour is pantone 1805 c (a dark red)

I want the design to convey the nature of our business as a strategic technology innovation company, but yet still be professional. We are funky vibey and work from an industrial style office in a vibey designer dominat part of town. Though are clients include large banks and corporate clients too.

The information that needs to be on the card is in attached word document (but doesn't have to be in this order or format)

Final version needs to be supplied in PNG preview, as well as PSD file format (or other editable file version) so that personal information on card can be easily edited and reprinted.

Target Market(s)

CEO's of small to medium size companies
Marketing Managers of large coporates
Account managers of Digital Agencies

Industry/Entity Type

Business

Requirements
Must have
• 86x54mm will be cut in rounded corner credit card size format (Except if you recommend otherwise in your design)
Nice to have
• Some kind of background transparency combined with the pantone colour that gives the card some dimension and depth. But no gradient fills please :-)
Should not have
• Basic gradient fills
• Clipart

```html
<!DOCTYPE html>
<html lang="en">
<head>
<meta charset="utf-8">
<title>Vantoro Business Card – Front and Back</title>
<link rel="stylesheet" href="https://fonts.googleapis.com/css2?family=Arimo:wght@400;700&family=Kalam:wght@400&display=swap">
<style>
  :root {
    --brand-red: #9c0610;
    --brand-red-deep: #8c0309;
    --paper: #ffffff;
    --ink: #1a1a1a;
    --stage-light: #dedede;
    --stage-dark: #c6c6c6;
  }
  * { margin: 0; padding: 0; box-sizing: border-box; }
  html, body { width: 1200px; height: 675px; overflow: hidden; }
  body {
    position: relative;
    background: radial-gradient(ellipse at 50% 45%, var(--stage-light), var(--stage-dark));
    font-family: "Arimo", Arial, sans-serif;
  }

  .side-tag {
    position: absolute;
    background: var(--brand-red);
    color: var(--paper);
    font-family: "Kalam", cursive;
    font-size: 62px;
    display: flex; align-items: center; justify-content: center;
  }
  .side-tag--front { left: 0; top: 77px; width: 213px; height: 95px; border-radius: 0 7px 7px 0; }
  .side-tag--back { right: 0; top: 480px; width: 223px; height: 95px; border-radius: 7px 0 0 7px; }

  .card {
    position: absolute;
    left: 387px;
    width: 450px;
    border-radius: 14px;
    overflow: hidden;
    background: var(--paper);
  }

  /* Front */
  .card--front { top: 18px; height: 282px; }
  .front-field { position: absolute; left: 0; top: 0; width: 450px; height: 251px; background: var(--brand-red); }
  .front-tab-top {
    position: absolute; left: 129px; top: 0; width: 176px; height: 11px;
    background: var(--paper); border-radius: 0 0 4px 4px;
  }
  .front-tab-bottom {
    position: absolute; left: 129px; top: 251px; width: 176px; height: 20px;
    background: var(--brand-red); border-radius: 0 0 4px 4px;
  }
  .brand-lockup { position: absolute; left: 122px; top: 124px; width: 246px; text-align: right; color: var(--paper); }
  .brand-name { display: block; font-weight: 700; font-size: 46px; line-height: 46px; letter-spacing: -1px; text-align: center; }
  .brand-tagline { display: block; font-size: 13px; margin-top: 4px; padding-right: 8px; }

  /* Back */
  .card--back { top: 333px; height: 275px; }
  .back-panel {
    position: absolute; left: 0; top: 0; width: 273px; height: 275px;
    background: var(--brand-red-deep);
  }
  .back-panel-lip {
    position: absolute; left: 270px; top: 44px; width: 13px; height: 182px;
    background: var(--brand-red-deep); border-radius: 0 4px 4px 0;
  }
  .back-panel-notch {
    position: absolute; left: 0; top: 49px; width: 16px; height: 176px;
    background: var(--paper); border-radius: 0 4px 4px 0;
  }
  .holder {
    position: absolute; left: 30px; top: 70px; width: 230px; text-align: center; color: var(--paper);
  }
  .holder-brand { display: block; font-weight: 700; font-size: 34px; line-height: 40px; margin-bottom: 22px; }
  .holder-name { display: block; font-family: "Kalam", cursive; font-size: 30px; line-height: 32px; }
  .holder-role { display: block; font-size: 11px; letter-spacing: 3.5px; margin-top: -2px; }

  .contact { position: absolute; left: 296px; top: 78px; color: var(--ink); list-style: none; }
  .contact li { font-size: 12.5px; letter-spacing: 0.8px; line-height: 21.5px; }
  .contact li.contact-plain { letter-spacing: 0.2px; line-height: 19px; }
  .company { position: absolute; left: 297px; top: 165px; color: var(--ink); }
  .company-name { display: block; font-size: 11.5px; }
  .company-address { display: block; font-size: 7.5px; line-height: 8.5px; margin-top: 1px; }
</style>
</head>
<body>
  <div class="side-tag side-tag--front">Front</div>

  <section class="card card--front" aria-label="Card front">
    <div class="front-field"></div>
    <div class="front-tab-top"></div>
    <div class="front-tab-bottom"></div>
    <div class="brand-lockup">
      <span class="brand-name">Vantoro</span>
      <span class="brand-tagline">Strategic Innovation</span>
    </div>
  </section>

  <section class="card card--back" aria-label="Card back">
    <div class="back-panel"></div>
    <div class="back-panel-lip"></div>
    <div class="back-panel-notch"></div>
    <div class="holder">
      <span class="holder-brand">Vantoro</span>
      <span class="holder-name">Daniel Marsh</span>
      <span class="holder-role">Founder &amp; MD</span>
    </div>
    <ul class="contact">
      <li>0821457390</li>
      <li>010 482 3361</li>
      <li class="contact-plain">www.vantoro.com</li>
      <li class="contact-plain">daniel@vantoro.com</li>
    </ul>
    <div class="company">
      <span class="company-name">Vantoro (Pty) Ltd</span>
      <span class="company-address">SUITE 214, 18 RIVERSTONE RD.<br>PARKHURST, JHB, RSA</span>
    </div>
  </section>

  <div class="side-tag side-tag--back">Back</div>
</body>
</html>
```